Grand Opening of Rosie's Tap, a craft beer bar in mountains of Payson AZ. Rosie is our black lab.

We need a card designed to advertise the grand opening of Rosie's Tap. It is a craft beer bar (we do not make our own beer but will highlight local beer) located next to Summit Lanes (which has also been rebranded). We will be serving craft beer and spirited drinks, along with a great burger (Rosie's Burger) and other bar food. The interior is a little industrial (corregated metal bar front) with a warm feel. We are trying to appeal to a more upscale crowd without being snobby. We would like it to be family friendly during the day.

Reason: I'm extending the deadline by 1 day so I have time to review updates. Thank you all for submissions!

```html
<!DOCTYPE html>
<html lang="en">
<head>
<meta charset="utf-8">
<title>Rosie's Tap – Grand Opening</title>
<link rel="stylesheet" href="https://fonts.googleapis.com/css2?family=Alegreya+SC:wght@400;700&family=Noticia+Text&family=Oswald:wght@500&display=swap">
<style>
  :root {
    --wood-dark: #4a2c18;
    --wood-mid: #6b4328;
    --wood-light: #80563a;
    --metal-dark: #6f7276;
    --metal-light: #b9bcbf;
    --gold-dark: #a8721c;
    --gold: #e2b04a;
    --gold-light: #f7dc8e;
    --black: #161616;
    --charcoal: #3a3a3a;
    --red-dark: #6e0a0a;
    --red: #c8201e;
    --cream: #f3ecd6;
    --white: #ffffff;
  }
  html, body {
    margin: 0;
    padding: 0;
    width: 1200px;
    height: 800px;
    overflow: hidden;
    background: var(--wood-dark);
  }
  .card {
    position: relative;
    width: 1200px;
    height: 800px;
    overflow: hidden;
    font-family: "Alegreya SC", Georgia, serif;
    color: var(--white);
  }
  .card p, .card h1, .card h2 { margin: 0; }
  .metal-band {
    position: absolute;
    left: 0;
    width: 1200px;
    background: linear-gradient(180deg, var(--metal-light), var(--metal-dark) 50%, var(--metal-light));
  }
  .metal-band--top { top: 0; height: 150px; }
  .metal-band--bottom { bottom: 0; height: 110px; }
  .wood-wall {
    position: absolute;
    left: 0;
    top: 148px;
    width: 1200px;
    height: 544px;
    background: linear-gradient(90deg, var(--wood-mid), var(--wood-light) 30%, var(--wood-mid) 55%, var(--wood-light) 80%, var(--wood-mid));
  }
  .laurel {
    position: absolute;
    background: linear-gradient(180deg, var(--cream), #e6d6a8 70%, var(--gold));
    border-radius: 60% 40% 50% 50%;
    opacity: 0.9;
  }
  .laurel--left { left: 62px; top: 345px; width: 150px; height: 345px; }
  .laurel--right { left: 1012px; top: 345px; width: 130px; height: 320px; }
  .shapes {
    position: absolute;
    inset: 0;
  }
  .headline-plaque {
    position: absolute;
    left: 293px;
    top: 38px;
    width: 614px;
    height: 132px;
    display: flex;
    align-items: center;
    justify-content: center;
    font-family: "Oswald", "Arial Narrow", sans-serif;
    font-weight: 500;
    font-size: 70px;
    line-height: 1;
    letter-spacing: 2px;
    white-space: nowrap;
  }
  .bar-name {
    position: absolute;
    left: 0;
    top: 178px;
    width: 1200px;
    text-align: center;
    font-family: "Noticia Text", Georgia, serif;
    font-weight: 400;
    font-size: 152px;
    line-height: 1;
    white-space: nowrap;
    text-shadow: 0 3px 6px rgba(0,0,0,0.35);
  }
  .event-date {
    position: absolute;
    left: 405px;
    top: 395px;
    width: 390px;
    text-align: center;
    font-weight: 700;
    line-height: 1;
    white-space: nowrap;
  }
  .event-date__day { display: block; font-size: 42px; }
  .event-date__time { display: block; font-size: 24px; text-align: right; padding-right: 80px; margin-top: 2px; }
  .lineup {
    position: absolute;
    left: 0;
    top: 512px;
    width: 1200px;
    text-align: center;
    font-size: 31px;
    line-height: 38px;
    white-space: nowrap;
    text-shadow: 0 2px 4px rgba(0,0,0,0.4);
  }
  .drink-special {
    position: absolute;
    left: 396px;
    top: 692px;
    width: 402px;
    text-align: center;
    line-height: 1.15;
    white-space: nowrap;
  }
  .drink-special__price { display: block; font-size: 30px; }
  .drink-special__note { display: block; font-size: 23px; }
  .burger-badge {
    position: absolute;
    left: 955px;
    top: 643px;
    width: 150px;
    text-align: center;
    font-weight: 700;
    font-size: 25px;
    line-height: 1.1;
  }
</style>
</head>
<body>
<main class="card">
  <div class="metal-band metal-band--top" role="img" aria-label="Corrugated metal panel"></div>
  <div class="wood-wall" role="img" aria-label="Warm wooden plank wall"></div>
  <div class="metal-band metal-band--bottom" role="img" aria-label="Corrugated metal panel"></div>

  <div class="laurel laurel--left" role="img" aria-label="Golden wheat laurel branch"></div>
  <div class="laurel laurel--right" role="img" aria-label="Golden wheat laurel branch"></div>

  <svg class="shapes" width="1200" height="800" viewBox="0 0 1200 800" aria-hidden="true">
    <defs>
      <linearGradient id="gold-rim" x1="0" y1="0" x2="1" y2="1">
        <stop offset="0" stop-color="#f7dc8e"/>
        <stop offset="0.5" stop-color="#e2b04a"/>
        <stop offset="1" stop-color="#a8721c"/>
      </linearGradient>
      <linearGradient id="plaque-fill" x1="0" y1="0" x2="0" y2="1">
        <stop offset="0" stop-color="#3a3a3a"/>
        <stop offset="1" stop-color="#161616"/>
      </linearGradient>
      <linearGradient id="red-fill" x1="0" y1="0" x2="1" y2="0">
        <stop offset="0" stop-color="#6e0a0a"/>
        <stop offset="0.6" stop-color="#c8201e"/>
        <stop offset="1" stop-color="#6e0a0a"/>
      </linearGradient>
    </defs>

    <!-- headline plaque -->
    <rect x="283" y="28" width="634" height="152" rx="76" fill="url(#gold-rim)"/>
    <rect x="293" y="38" width="614" height="132" rx="66" fill="url(#plaque-fill)"/>
    <g fill="#e2b04a">
      <circle cx="348" cy="38" r="5"/><circle cx="591" cy="38" r="5"/><circle cx="853" cy="38" r="5"/>
      <circle cx="348" cy="170" r="5"/><circle cx="591" cy="170" r="5"/><circle cx="853" cy="170" r="5"/>
      <circle cx="293" cy="103" r="5"/><circle cx="907" cy="103" r="5"/>
    </g>

    <!-- date ribbon -->
    <polygon points="430,420 350,428 382,462 345,502 440,492" fill="#161616" stroke="url(#gold-rim)" stroke-width="5"/>
    <polygon points="770,420 850,428 818,462 855,502 760,492" fill="#161616" stroke="url(#gold-rim)" stroke-width="5"/>
    <polygon points="405,380 795,380 795,482 405,482" fill="url(#plaque-fill)" stroke="url(#gold-rim)" stroke-width="6"/>

    <!-- drink special pill -->
    <rect x="388" y="676" width="418" height="100" rx="50" fill="url(#gold-rim)"/>
    <rect x="396" y="684" width="402" height="84" rx="42" fill="url(#red-fill)"/>

    <!-- burger starburst -->
    <polygon fill="url(#plaque-fill)" stroke="url(#gold-rim)" stroke-width="7" points="1030,572 1050.7,594.7 1080,585.4 1086.6,615.4 1116.6,622 1107.3,651.3 1130,672 1107.3,692.7 1116.6,722 1086.6,728.6 1080,758.6 1050.7,749.3 1030,772 1009.3,749.3 980,758.6 973.4,728.6 943.4,722 952.7,692.7 930,672 952.7,651.3 943.4,622 973.4,615.4 980,585.4 1009.3,594.7"/>
  </svg>

  <h2 class="headline-plaque">GRAND OPENING</h2>
  <h1 class="bar-name">Rosie's Tap</h1>

  <p class="event-date">
    <span class="event-date__day">September 19th</span>
    <span class="event-date__time">at 4pm.</span>
  </p>

  <p class="lineup">
    Live entertainment by:<br>
    Band Nine on Friday night<br>
    Nick Fiorello &amp; the Hot Espressos<br>
    on Saturday night and Sunday afternoon.
  </p>

  <p class="drink-special">
    <span class="drink-special__price">$3 Craft beers</span>
    <span class="drink-special__note">and Spirited Drinks all weekend</span>
  </p>

  <p class="burger-badge">GREAT<br>BURGERS</p>
</main>
</body>
</html>
```